Desert Basin Company Brochure

**** UPDATE 2-8-2014 ****

Size should be 11" X 17" or larger (tri or bi fold).

We're going to let the contest run it's full duration to allow for more time spent on designs.

No black backgrounds.

Consideration should be given to having the text be easy to read and in a nice, organized format.

*****************************

We're looking for an eye-catching, colorful brochure that will explain what we do, who we are... and what sets us apart from the competition.

Our company provides swimming pool service, repair, and custom renovations throughout the Phoenix, Arizona metropolitan area. These brochures will be hand-delivered to each prospective customer we visit.

The brochure will include images of our work, product logos, and a unique design that separates our company apart from the rest.

The brochure should be tri-fold. Although, if a designer wants to (or has better ideas) for a different lay-out, then we're open to seeing what can be done.

Colors we like: Blue, White, Silver, Copper, Green (accent color)

We like designs that are unique/different. Professional. Creative. Sleek. Sexy. Custom. We don't want the brochure to be "pretentious". We'd like for these brochures to leave a lasting impression with our prospective clients... and hopefully earn us more business.

We don't want the brochure to be too wordy, however if the designer feels we need to cut back (or add), let us know.

Our motto is "Every Ripple Counts".

You can view some of our projects, and what we're about either at our website (tidewellpools.example), Facebook (www.facebook/tidewellpools), or Google+ (https://plus.google.com/+Tidewellpools). Thank you!

- Print-

(Front) Logo

Service - Repair - Renovation
555-347-9180
tidewellpools.example
service@tidewellpools.example
Like Us On Facebook! Facebook LOGO
Google Plus LOGO

(Body) Why Choose Us?

Thank you for the opportunity for our company to become your pool service provider!

We’re committed to providing the best customer service possible! At the end of the day you want your pool to be clean, clear, operational, and for your service provider to be available when you need them!

We’re licensed with the Sonoran Trades Licensing Board, Bonded, and Fully Insured.
A+ reviews with the Fair Merchant Council, Corra's Picks, Brivo, Olt, Facebook, and Google!
All technicians are employees... not sub-contractors! Our employees are hard working, dependable, professional, and expected to follow our strict protocol for servicing your pool.
Flat-fee service rates! Any additional equipment repairs, maintenance, or chemical implementations are directly authorized by you!
No contracts! Our Service Level Agreement Form allows you to select your desired level of authorization for equipment repairs, filter maintenance, and extra chemical implementation programs.
Our uniformed technicians arrive in distinctive, clean GPS-tracked company trucks.
We leave detailed service slips after each service visit. In addition, all service visit information is electronically recorded and stored.
Easy, online account management to view and pay invoices or authorize estimates.
Invoices, estimates, questions, pictures, and video are communicated via e-mail!
Free service calls to diagnose equipment issues outside of our normal service.
10% Service Client Discount for all repairs and replacement items.
Tidewell Pools knows the importance of communication! We’re available by phone, email, or text all days of the week.

(Body) Our Methodology

We believe in 5 important factors in maintaining a clean, clear, and operational pool...

Good, Clean Water! Our local water supply contains high amounts of minerals. Pool chemicals add to this problem in a short amount of time. Our philosophy is to use the least amount of chemicals possible to achieve optimal water balance.
Efficient Water Flow! The invention of variable-speed pumps has enabled the ability to "dial in" proper water flow... while driving down energy costs.
Proper Filtration! Today’s high-capacity cartridge filters provide great filtration, save on wasted water from backwashing sand filters, and eliminate the need for water flow-restricting backwash valves.
Functioning Cleaning System! Having a working automatic cleaning system is vital in keeping the pool surface clean of debris and dirt... and free of staining.
A Dependable And Professional Pool Maintenance Technician! Our job is to not only oversee all of the items listed above... but to make sure your pool is in the best condition possible!

(Body) Equipment Repair & Installation

We’re educated on all phases of swimming pool equipment repair and installation... with a focus on energy-efficiency and optimum performance!

We’re an VRE & MQW Authorized Installer of variable-speed pool pumps. VRE & MQW trust us to properly install and calibrate all variable-speed pumps. We've been equipped to handle the new industry standards on variable-speed pumps since Arizona law went into effect January 1st, 2011.
We’re experts at acid washes and erasing the mineral build-up off of waterlines. All work is done in-house with our customized cleaning rig and trailer.
Heating systems. New efficiency standards have made installation and operation more affordable than ever.
Remote control automation systems. Technology now allows the user to easily view and control their entire pool system via a remote home computer, tablet, or phone!
Brilliant, color-changing LED lighting for pools and spas! The benefits of LED include brighter and broader displays... while lasting much longer than your typical light bulbs.
Salt systems provide a soft-water experience! In addition to the benefit of better feeling water, salt systems generate plenty of chlorine to keep your pool sanitized.

(Body) About Us

A native to Phoenix, Daniel Harrow founded Tidewell Pools in 2000. Our company was built from the ground up by way of hard work, word of mouth, and determination. Our company will always remain firmly grounded, and continue to develop systems that put our customers first!

Our philosophy is to treat every pool as if it were our own, run an efficient and organized business, and care for our employees.

Tidewell Pools is a yearly, proud contributor to the Saguaro Youth Clinic Swim Smart Day. Please educate and watch all children around water... every accident can be avoided.

(Back) Contact Us

Office: 555-347-9180 | Fax: 555-347-9186 | Email: service@tidewellpools.example
tidewellpools.example

Office / Warehouse Location
41572 West 8th Street, Suite 4
Phoenix, Arizona 85999
(NW of 8th Street & Mesquite Ridge Road)

AZ ROC: 731150, 731151, 731152, 604378

Target Market(s)

We target a market of pool owners, which typically have more disposable income.

30 - 75 years old.

Our clients range from first-time home buyers, self-employed, business professionals, doctors, landlords, thousandaires, millionaires.

Industry/Entity Type

Pool Service

Font styles to use
Serif

Colors
0355a3
cfdfed
ffffff
3176b5
eaf1f7

Requirements
Must have
• Must use provided images. We've included a few pool pictures, and will let you decide which ones to incorporate throughout the brochure.

Logos Used:
Tidewell Pools
Hydrovel
FMC
Corra's Picks
VRE
MQW
Saguaro Youth Clinic
Google+
Facebook

Image pic of some of our trucks.

Nice to have
• Equipment images worked in.
Should not have
• Cartoonish fonts or design. No "Love" hearts!!

```html
<!DOCTYPE html>
<html lang="en">
<head>
<meta charset="utf-8">
<title>Tidewell Pools – Trifold Brochure Inside</title>
<link href="https://fonts.googleapis.com/css2?family=Oswald:wght@500;600&family=Open+Sans:wght@400;600;700&display=swap" rel="stylesheet">
<style>
  :root {
    --stage: #e8e8e8;
    --panel-blue: #2b3b93;
    --panel-blue-deep: #222f7e;
    --title-navy: #1c2766;
    --ice: #cfdfed;
    --mist: #eaf1f7;
    --white: #ffffff;
    --water-top: #1f6fbf;
    --water-mid: #4aa6d2;
    --deck-sand: #b8a688;
    --frame-blue: #3176b5;
  }
  * { box-sizing: border-box; margin: 0; padding: 0; }
  html, body {
    width: 1200px; height: 800px; overflow: hidden;
    background: var(--stage);
    font-family: "Open Sans", Arial, sans-serif;
  }
  .brochure {
    position: absolute; left: 28px; top: 30px;
    width: 1144px; height: 740px;
    display: grid; grid-template-columns: repeat(3, 1fr);
    box-shadow: 0 10px 30px rgba(0,0,0,.18);
  }
  .panel { position: relative; overflow: hidden; }
  .panel--text {
    background: linear-gradient(160deg, var(--panel-blue) 0%, var(--panel-blue-deep) 100%);
    color: var(--white);
    padding: 34px 28px 26px;
  }
  .panel-heading {
    font-family: "Oswald", "Arial Narrow", sans-serif;
    font-weight: 500; font-size: 17px; letter-spacing: 1px;
    text-transform: uppercase; color: var(--ice);
    margin-bottom: 10px;
  }
  .panel-heading + .intro, .intro { font-size: 12px; line-height: 1.55; margin-bottom: 10px; color: var(--mist); }
  .feature-list { list-style: none; font-size: 12px; line-height: 1.5; color: var(--mist); }
  .feature-list li { position: relative; padding-left: 14px; margin-bottom: 5px; }
  .feature-list li::before {
    content: ""; position: absolute; left: 0; top: 7px;
    width: 5px; height: 5px; background: var(--ice);
  }
  .section + .section { margin-top: 26px; }

  .gallery {
    position: absolute; left: 28px; right: 28px; bottom: 28px;
    display: grid; grid-template-columns: 1fr 1fr; gap: 14px;
  }
  .gallery-photo {
    height: 112px; border: 4px solid var(--frame-blue);
  }
  .gallery-photo--lake { background: linear-gradient(180deg, #9cc3e0 0%, #6f9cb8 45%, #c9b898 100%); }
  .gallery-photo--spa { background: linear-gradient(180deg, #6c8a6a 0%, #3ea6c4 50%, #c8b79a 100%); }

  .panel--photo { background: var(--white); }
  .hero-photo {
    position: absolute; inset: 0;
    background: linear-gradient(180deg, var(--water-top) 0%, var(--water-mid) 38%, #5f9db0 58%, var(--deck-sand) 100%);
  }
  .title-band {
    position: absolute; left: -60px; top: 470px; width: 560px; height: 160px;
    transform: rotate(-32deg); transform-origin: center;
    background: var(--white);
  }
  .hero-title {
    position: absolute; left: 70px; top: 430px;
    transform: rotate(-32deg); transform-origin: left top;
    display: flex; flex-direction: column; align-items: flex-start; gap: 8px;
  }
  .hero-title span {
    background: var(--title-navy); color: var(--white);
    font-family: "Oswald", "Arial Narrow", sans-serif; font-weight: 600;
    font-size: 44px; line-height: 1; letter-spacing: 1px;
    padding: 8px 16px; text-transform: uppercase;
  }
  .hero-title span + span { margin-left: 40px; }
</style>
</head>
<body>
<main class="brochure">
  <section class="panel panel--text">
    <h2 class="panel-heading">Why Choose Us?</h2>
    <p class="intro">Thank you for the opportunity to become your pool service provider! We’re committed to the best customer service possible.</p>
    <ul class="feature-list">
      <li>Licensed with the Sonoran Trades Licensing Board, bonded, and fully insured.</li>
      <li>A+ reviews with the Fair Merchant Council, Corra's Picks, Brivo and Olt.</li>
      <li>All technicians are employees, not sub-contractors.</li>
      <li>Flat-fee service rates with no contracts.</li>
      <li>Uniformed technicians in clean, GPS-tracked company trucks.</li>
      <li>Detailed service slips left after each visit.</li>
      <li>Easy online account management to view and pay invoices.</li>
      <li>Free service calls to diagnose equipment issues.</li>
      <li>10% service client discount on all repairs.</li>
      <li>Tidewell Pools is available by phone, email, or text every day of the week.</li>
    </ul>
    <div class="gallery">
      <div class="gallery-photo gallery-photo--lake" role="img" aria-label="Photo of a finished backyard pool overlooking a lake"></div>
      <div class="gallery-photo gallery-photo--spa" role="img" aria-label="Photo of a renovated pool and spa with a stone deck"></div>
    </div>
  </section>

  <section class="panel panel--photo">
    <div class="hero-photo" role="img" aria-label="Photo of clear blue pool water rippling over a stone edge"></div>
    <div class="title-band"></div>
    <h1 class="hero-title"><span>Another Title</span><span>Goes Here!</span></h1>
  </section>

  <section class="panel panel--text">
    <div class="section">
      <h2 class="panel-heading">Our Methodology</h2>
      <p class="intro">We believe in five important factors in maintaining a clean, clear, and operational pool.</p>
      <ul class="feature-list">
        <li>Good, clean water with the least chemicals possible.</li>
        <li>Efficient water flow from variable-speed pumps.</li>
        <li>Proper filtration with high-capacity cartridge filters.</li>
        <li>A functioning automatic cleaning system.</li>
        <li>A dependable, professional maintenance technician.</li>
      </ul>
    </div>
    <div class="section">
      <h2 class="panel-heading">Equipment Repair &amp; Installation</h2>
      <p class="intro">We’re educated on all phases of pool equipment repair and installation, with a focus on energy-efficiency.</p>
      <ul class="feature-list">
        <li>VRE &amp; MQW authorized installer of variable-speed pumps.</li>
        <li>Acid washes and waterline mineral removal done in-house.</li>
        <li>Heating systems, automation, LED lighting and salt systems.</li>
      </ul>
    </div>
  </section>
</main>
</body>
</html>
```